Business Card, A4 Letter Head and DL Envelope for Brandvelle

We are looking for a design for our Business Card, A4 Letter Head and DL Envelope.

Brandvelle is a distributor of promotional products. We specialize in a range of branded promotional products, these include pens, polo shirts, key rings, drink bottles, uniforms and bags to name a few. We are experts in marketing and assist companies in choosing the right promotional product for their needs. We will predominately be an online business where customers visit our website and browse our range of promotional products and branding options.

Our colours are black, red, white and grey.

Files must be supplied in eps, pdf and ai format.

Please display the following information:
Derek Halloway
Account Manager
Suite xxx, 212 Ferrow Lane Melbourne, Victoria 3000
Phone +61 3 5550 1827
Mobile +61 455 016 342
sales@brandvelle-example.com.au
www.brandvelle-example.com.au

```html
<!DOCTYPE html>
<html lang="en">
<head>
<meta charset="utf-8">
<title>Brandvelle Stationery</title>
<link rel="stylesheet" href="https://fonts.googleapis.com/css2?family=Jost:wght@400;500&family=Michroma&display=swap">
<style>
  :root {
    --red: #c01c24;
    --ink: #3a3a3a;
    --grey: #6b6b6b;
    --paper: #ffffff;
    --bg-dark: #505050;
    --bg-light: #8c8c8c;
    --faint: #f0f0f0;
  }
  * { margin: 0; padding: 0; box-sizing: border-box; }
  html, body { width: 1200px; height: 1000px; overflow: hidden; }
  body {
    position: relative;
    background: linear-gradient(135deg, var(--bg-dark) 0%, var(--bg-light) 100%);
    font-family: "Jost", Arial, sans-serif;
    color: var(--ink);
  }
  .sheet { position: absolute; background: var(--paper); box-shadow: 2px 3px 6px rgba(0,0,0,.35); overflow: hidden; }
  .abs { position: absolute; }
  .band { position: absolute; background: var(--red); }
  .brand { position: absolute; display: flex; align-items: center; white-space: nowrap; }
  .brand-dot { border-radius: 50%; background: var(--red); flex: none; }
  .brand-name { color: var(--ink); font-weight: 500; letter-spacing: .02em; text-transform: uppercase; }
  .faint-mark { position: absolute; border-radius: 50%; background: var(--faint); }
  .contact-list { position: absolute; list-style: none; }
  .contact-list li { display: flex; align-items: center; white-space: nowrap; }
  .icon { border-radius: 50%; background: var(--red); color: #fff; display: inline-flex; align-items: center; justify-content: center; flex: none; }
  .red-text { color: var(--red); }

  /* Letterhead */
  .letterhead { left: 28px; top: 32px; width: 524px; height: 678px; }
  .letterhead .top-band { left: 0; top: 0; width: 100%; height: 34px; }
  .letterhead .brand { left: 32px; top: 52px; gap: 10px; }
  .letterhead .brand-dot { width: 34px; height: 34px; }
  .letterhead .brand-name { font-size: 17px; }
  .letterhead .contact-list { left: 400px; top: 49px; border-left: 1px solid var(--red); padding-left: 4px; font-size: 6.5px; line-height: 8px; }
  .letterhead .icon { width: 6px; height: 6px; font-size: 4.5px; margin-right: 3px; }
  .letterhead .faint-mark { left: 360px; top: 482px; width: 138px; height: 138px; }
  .letterhead .foot-line { top: 655px; height: 6px; }
  .letterhead .foot-address { left: 172px; top: 653px; font-size: 7px; white-space: nowrap; }

  /* Business card front */
  .card-front { left: 616px; top: 79px; width: 414px; height: 247px; }
  .card-front .panel { left: 196px; top: 0; width: 218px; height: 100%; }
  .card-front .holder { left: 214px; top: 14px; color: #ececec; }
  .card-front .holder-name { font-family: "Michroma", Arial, sans-serif; font-size: 16px; line-height: 24px; }
  .card-front .holder-role { font-size: 13px; line-height: 16px; }
  .card-front .brand { left: 22px; top: 58px; flex-direction: column; gap: 8px; width: 150px; }
  .card-front .brand-dot { width: 54px; height: 54px; }
  .card-front .brand-name { font-size: 15px; }
  .card-front .contact-list { left: 21px; top: 143px; font-size: 11px; line-height: 15px; color: #222; }
  .card-front .icon { width: 11px; height: 11px; font-size: 7px; margin-right: 4px; }
  .card-front .address { left: 21px; top: 193px; font-size: 11.5px; line-height: 15px; }

  /* Business card back */
  .card-back { left: 715px; top: 382px; width: 415px; height: 248px; }
  .card-back .brand { left: 0; top: 30px; width: 100%; flex-direction: column; gap: 22px; }
  .card-back .brand-dot { width: 96px; height: 96px; }
  .card-back .brand-name { font-size: 27px; }
  .card-back .foot { left: 0; top: 196px; width: 100%; height: 52px; display: flex; align-items: center; justify-content: center; color: #fff; font-size: 13px; }
  .card-back .foot .icon { background: #fff; color: var(--red); width: 12px; height: 12px; font-size: 7px; margin-right: 5px; }

  /* Envelope */
  .envelope { left: 249px; top: 723px; width: 587px; height: 257px; }
  .envelope .top-band { left: 0; top: 0; width: 100%; height: 34px; }
  .envelope .brand { left: 35px; top: 62px; gap: 6px; }
  .envelope .brand-dot { width: 24px; height: 24px; }
  .envelope .brand-name { font-size: 12px; }
  .envelope .return { left: 38px; top: 93px; border-left: 1px solid var(--red); padding-left: 3px; font-size: 7px; line-height: 9px; }
  .envelope .icon { width: 7px; height: 7px; font-size: 5px; margin-right: 3px; }
  .envelope .faint-mark { left: 478px; top: 144px; width: 74px; height: 74px; }
  .envelope .foot-band { left: 0; top: 240px; width: 100%; height: 8px; }
</style>
</head>
<body>

<section class="sheet letterhead" aria-label="A4 letterhead">
  <div class="band top-band"></div>
  <div class="brand"><span class="brand-dot"></span><span class="brand-name">Brandvelle</span></div>
  <ul class="contact-list">
    <li><span class="icon">M</span>+61 455 016 342</li>
    <li><span class="icon">T</span>+61 3 5550 1827</li>
    <li><span class="icon">e</span>sales@brandvelle-example.com.au</li>
    <li><span class="icon">w</span>www.brandvelle-example.com.au</li>
  </ul>
  <div class="faint-mark"></div>
  <div class="band foot-line" style="left:0;width:160px"></div>
  <div class="band foot-line" style="left:363px;width:161px"></div>
  <p class="abs foot-address red-text">Suite xxx, 212 Ferrow Lane Melbourne, Victoria 3000</p>
</section>

<section class="sheet card-front" aria-label="Business card front">
  <div class="band panel"></div>
  <div class="abs holder">
    <p class="holder-name">Derek Halloway</p>
    <p class="holder-role">Account Manager</p>
  </div>
  <div class="brand"><span class="brand-dot"></span><span class="brand-name">Brandvelle</span></div>
  <ul class="contact-list">
    <li><span class="icon">M</span>+61 455 016 342</li>
    <li><span class="icon">T</span>+61 3 5550 1827</li>
    <li><span class="icon">e</span>sales@brandvelle-example.com.au</li>
  </ul>
  <p class="abs address red-text">Suite xxx, 212 Ferrow Lane<br>Melbourne, Victoria 3000</p>
</section>

<section class="sheet card-back" aria-label="Business card back">
  <div class="brand"><span class="brand-dot"></span><span class="brand-name">Brandvelle</span></div>
  <div class="band foot"><span class="icon">w</span>www.brandvelle-example.com.au</div>
</section>

<section class="sheet envelope" aria-label="DL envelope">
  <div class="band top-band"></div>
  <div class="brand"><span class="brand-dot"></span><span class="brand-name">Brandvelle</span></div>
  <div class="abs return">
    <p style="display:flex;align-items:center"><span class="icon">T</span>+61 3 5550 1827</p>
    <p class="red-text">Suite xxx, 212 Ferrow Lane<br>Melbourne, Victoria 3000</p>
  </div>
  <div class="faint-mark"></div>
  <div class="band foot-band"></div>
</section>

</body>
</html>
```